Franchise Power Point

Looking to add a strong design element to a very basic power point presentation about how to find the ideal franchise match. My website is www.tallowbrookventuring.com and www.unitquest/KWendell

```html
<!DOCTYPE html>
<html lang="en">
<head>
<meta charset="utf-8">
<title>How to Find the Ideal Franchise Match – Slide Deck</title>
<link href="https://fonts.googleapis.com/css2?family=Poppins:wght@400;500;600;700;800&display=swap" rel="stylesheet">
<style>
:root{
  --yellow:#f8bb16;
  --navy:#213a6c;
  --blue:#24539b;
  --ink:#16181d;
  --night:#12141a;
  --paper:#ffffff;
  --mist:#f4f5f7;
  --grey-photo-a:#d9d9d9;
  --grey-photo-b:#6f6f6f;
  --step-blue:#2d56a4;
  --step-yellow:#fbd85c;
}
*{margin:0;padding:0;box-sizing:border-box}
html,body{width:1200px;height:2412px;overflow:hidden;background:#fff}
body{font-family:'Poppins',sans-serif;color:var(--ink)}
.deck{width:1200px;height:2412px;display:grid;grid-template-columns:595px 595px;grid-template-rows:repeat(7,336px);column-gap:10px;row-gap:10px}
.slide{position:relative;overflow:hidden;background:var(--paper)}
.slide.light{background:var(--mist)}
.slide.navy{background:var(--navy);color:#fff}
.slide.dark{color:#fff}
.backdrop{position:absolute;inset:0}
.backdrop.stars{background:radial-gradient(ellipse at 70% 110%,#3a4a66 0%,#1c2230 45%,#0d0f14 100%)}
.backdrop.sand{background:radial-gradient(ellipse at 50% 40%,#2a2b2e 0%,#17181b 60%,#0c0c0e 100%)}
.tagline{position:absolute;top:22px;right:16px;font-size:5.5px;font-weight:700;letter-spacing:.1px;text-transform:uppercase;color:var(--ink)}
.navy .tagline,.dark .tagline{color:#fff}
.brand{position:absolute;right:40px;bottom:18px;display:flex;align-items:center;gap:4px;font-size:13px;font-weight:600;color:var(--ink)}
.navy .brand,.dark .brand{color:#fff}
.brand .dot{width:6px;height:6px;border-radius:50%;background:var(--yellow)}
.hl{color:var(--yellow)}
.ph{position:absolute}
h1,h2,h3{font-weight:700;line-height:1.12}
.bullets{position:absolute;list-style:none}
.bullets li{position:relative;padding-left:12px;line-height:1.25;margin-bottom:4px}
.bullets li::before{content:"";position:absolute;left:0;top:.5em;width:3px;height:3px;border-radius:50%;background:currentColor}

/* 1 */
.cover-title{position:absolute;left:54px;top:60px;font-size:29px;color:#fff;line-height:1.05}
.portrait{left:50px;top:226px;width:76px;height:76px;border:2px solid var(--yellow);background:linear-gradient(160deg,#e8d3b8,#b99470)}
.contact{position:absolute;left:145px;top:243px;font-size:9px;line-height:1.15;color:#fff}
.contact strong{font-weight:700}
/* 2 */
.corner-block{position:absolute;left:0;top:0;width:226px;height:141px;background:var(--yellow)}
.thinker-photo{left:41px;top:52px;width:555px;height:140px;background:linear-gradient(90deg,#2b2b2b,#8a8a8a 45%,#e6e6e6)}
.smart-title{position:absolute;left:45px;top:216px;font-size:25px;color:var(--ink)}
/* 3 */
.side-bar{position:absolute;left:0;top:0;width:137px;height:100%;background:var(--yellow)}
.dream-title{position:absolute;left:46px;top:50px;font-size:25px;color:var(--ink)}
.city-photo{left:42px;top:158px;width:554px;height:141px;background:linear-gradient(180deg,#f2f2f2,#bdbdbd 55%,#5e5e5e)}
.city-photo + .brand{color:#fff}
/* 4 */
.big-title{position:absolute;left:51px;top:164px;font-size:38px;color:#fff;line-height:1.12}
/* 5 */
.hand-icon{left:50px;top:62px;width:130px;height:130px;background:linear-gradient(135deg,#f6f7f9,#d5efe7);border-radius:8px}
.approach-title{position:absolute;left:46px;top:206px;font-size:24px;color:var(--blue);line-height:1.15}
.step{position:absolute;width:203px;height:38px;border-radius:6px;display:flex;align-items:center;gap:12px;padding-left:16px;box-shadow:0 3px 6px rgba(0,0,0,.15);background:#fff;font-size:7px;line-height:1.2}
.step b{font-size:28px;font-weight:700;color:var(--step-blue);line-height:1}
.step.s2{background:var(--step-blue);color:#fff}.step.s2 b{color:#fff}
.step.s4{background:var(--step-yellow)}
/* 6 */
.chat-icon{left:54px;top:56px;width:82px;height:90px;background:linear-gradient(135deg,#5bc6a8,#f6b94a);border-radius:6px}
.slide-title{position:absolute;font-size:25px;color:var(--ink)}
.questions{font-size:8.5px;color:var(--ink)}
/* 7 */
.research-icon{left:45px;top:56px;width:113px;height:107px;background:linear-gradient(135deg,#d7ecf7,#7bb8dd);border-radius:6px}
.research{font-size:7.5px;color:var(--ink)}
/* 8 */
.brain-art{left:51px;top:68px;width:186px;height:198px;border-radius:50%;background:radial-gradient(circle,#f8bb16 0%,#f8bb16 45%,rgba(33,58,108,0) 70%)}
.decision{position:absolute;left:260px;right:0;top:134px;text-align:center}
.decision h2{font-size:31px;color:#fff}
.decision p{font-size:17px;margin-top:4px}
/* 9 */
.change-title{position:absolute;left:52px;top:113px;font-size:26px;color:var(--blue);line-height:1.05}
.change-sub{position:absolute;left:52px;top:185px;font-size:13px}
.stop-art{left:322px;top:69px;width:209px;height:209px;border-radius:50%;background:radial-gradient(circle,#f8bb16 0%,#f8bb16 35%,#fff 36%,#fff 58%,var(--navy) 59%)}
/* 10 */
.river{position:absolute;left:0;right:0;top:122px;text-align:center;font-size:25px;line-height:1.15;font-weight:400}
.river b{font-weight:700;color:var(--yellow)}
/* 11 */
.book-cover{left:62px;top:51px;width:192px;height:237px;background:linear-gradient(180deg,#1e5b74 0%,#3b7f96 35%,#f1f1f1 36%,#e4e4e4 100%)}
.booth{position:absolute;left:303px;top:125px;font-size:15px;line-height:1.25;color:#fff}
.booth b{font-weight:700}
/* 12,13 */
.thumb-art{width:135px;height:135px;border-radius:50%;background:radial-gradient(circle,#f7c7a8 0%,#f7c7a8 38%,rgba(248,187,22,.35) 40%,rgba(248,187,22,0) 70%)}
.dozen-title{position:absolute;font-size:38px;line-height:1.15}
.dozen{font-size:11px}
.thanks{position:absolute;left:0;right:0;top:152px;text-align:center;font-size:44px;font-weight:800;color:#fff;letter-spacing:.5px}
</style>
</head>
<body>
<main class="deck">

<section class="slide dark">
  <div class="backdrop stars" role="img" aria-label="Long-exposure photo of star trails circling the night sky"></div>
  <h1 class="cover-title">How to<br><span class="hl">Find the Ideal<br>Franchise</span><br>Match</h1>
  <div class="ph portrait" role="img" aria-label="Portrait photo of the presenter"></div>
  <p class="contact"><strong>Kara Wendell</strong><br>555.014.2290<br>kwendell@unitquest.com<br>http://www.tallowbrookventuring.com</p>
  <div class="brand" style="right:38px;bottom:30px;font-size:17px">UnitQuest<span class="dot"></span></div>
</section>

<section class="slide">
  <div class="corner-block"></div>
  <p class="tagline">Helping people realize their dream</p>
  <div class="ph thinker-photo" role="img" aria-label="Black and white photo of a thoughtful man with hand on chin"></div>
  <h2 class="smart-title">Smart Franchise<br>Decisions Using Logic<br>and Intuition</h2>
  <div class="brand">UnitQuest<span class="dot"></span></div>
</section>

<section class="slide">
  <div class="side-bar"></div>
  <p class="tagline">Helping people realize their dream</p>
  <h2 class="dream-title">Do not let your<br>Entrepreneurial Dream turn<br>a Technicians Nightmare</h2>
  <div class="ph city-photo" role="img" aria-label="Black and white photo of a city skyline"></div>
  <div class="brand">UnitQuest<span class="dot"></span></div>
</section>

<section class="slide dark">
  <div class="backdrop sand" role="img" aria-label="Dark photo of textured sand dunes"></div>
  <p class="tagline">Helping people realize their dream</p>
  <h2 class="big-title">Use <span class="hl">the<br>Educated</span><br>Approach</h2>
  <div class="brand">UnitQuest<span class="dot"></span></div>
</section>

<section class="slide light">
  <p class="tagline">Helping people realize their dream</p>
  <div class="ph hand-icon" role="img" aria-label="Illustration of a raised hand holding a pencil"></div>
  <h2 class="approach-title">What is the<br>Educated<br>Approach?</h2>
  <div class="step s1" style="left:246px;top:81px"><b>1</b><span>First Define<br>the Ideal Fit</span></div>
  <div class="step s2" style="left:305px;top:138px"><b>2</b><span>Focus on options that<br>fit your strengths</span></div>
  <div class="step s3" style="left:224px;top:199px"><b>3</b><span>Focus on options that will meet<br>your lifestyle and financial goals<br>while reducing risk</span></div>
  <div class="step s4" style="left:267px;top:265px"><b>4</b><span>Put yourself at the<br>center of the search</span></div>
  <div class="brand">UnitQuest<span class="dot"></span></div>
</section>

<section class="slide light">
  <p class="tagline">Helping people realize their dream</p>
  <div class="ph chat-icon" role="img" aria-label="Illustration of speech bubbles with question marks"></div>
  <h2 class="slide-title" style="left:201px;top:60px">Sample Key<br>Questions for the<br>Educated Approach</h2>
  <ul class="bullets questions" style="left:201px;top:176px;width:170px">
    <li>Proper investment level</li>
    <li>Skill set and background / personality matching</li>
    <li>Return goals – short, mid and long term</li>
    <li>Employee profile: numbers &amp; backgrounds</li>
    <li>Sales, marketing and advertising</li>
    <li>Concerns around the economy</li>
  </ul>
  <ul class="bullets questions" style="left:398px;top:176px;width:120px">
    <li>Need vs want</li>
    <li>Residual / Repeat / Reoccurring</li>
    <li>Status</li>
    <li>B2B vs B2C</li>
    <li>Full time vs part time vs. managed services</li>
  </ul>
  <div class="brand">UnitQuest<span class="dot"></span></div>
</section>

<section class="slide light">
  <p class="tagline">Helping people realize their dream</p>
  <div class="ph research-icon" role="img" aria-label="Illustration of a monitor with a magnifying glass and two people"></div>
  <h2 class="slide-title" style="left:192px;top:70px;font-size:26px">The<br>Research<br>Method</h2>
  <ul class="bullets research" style="left:203px;top:193px">
    <li>Define your ideal match</li>
    <li>Establish contact with target franchisor</li>
    <li>Work through their standard process</li>
    <li>Review FDD</li>
    <li>Validate with franchisees</li>
  </ul>
  <ul class="bullets research" style="left:418px;top:193px">
    <li>Explore financing options</li>
    <li>Discuss territory</li>
    <li>Put together cash flow projections</li>
    <li>Attend Discovery Day</li>
    <li>Make a decision</li>
  </ul>
  <div class="brand">UnitQuest<span class="dot"></span></div>
</section>

<section class="slide navy">
  <p class="tagline">Helping people realize their dream</p>
  <div class="ph brain-art" role="img" aria-label="Illustration of a yellow brain surrounded by sparkles"></div>
  <div class="decision"><h2>Decision Making</h2><p>Right Brain vs. Left Brain</p></div>
  <div class="brand">UnitQuest<span class="dot"></span></div>
</section>

<section class="slide">
  <p class="tagline">Helping people realize their dream</p>
  <h2 class="change-title">The human spirit<br>resist’s change</h2>
  <p class="change-sub">The human spirit resist’s change</p>
  <div class="ph stop-art" role="img" aria-label="Illustration of a yellow raised hand inside a prohibition sign"></div>
  <div class="brand">UnitQuest<span class="dot"></span></div>
</section>

<section class="slide dark">
  <div class="backdrop sand" role="img" aria-label="Dark photo of textured sand dunes"></div>
  <p class="tagline">Helping people realize their dream</p>
  <p class="river">Are you <b>the</b><br><b>dam</b> or are you<br><b>the River</b>?</p>
  <div class="brand">UnitQuest<span class="dot"></span></div>
</section>

<section class="slide navy">
  <p class="tagline">Helping people realize their dream</p>
  <div class="ph book-cover" role="img" aria-label="Cover of a step-by-step guide book for choosing a franchise"></div>
  <p class="booth">Stop by <b>my Booth,</b> Ask Me<br>ANY <b>Question</b> and<br>Receive a <b>Free Copy</b> of<br>The <b>Owner's Field Guide</b></p>
  <div class="brand">UnitQuest<span class="dot"></span></div>
</section>

<section class="slide">
  <p class="tagline">Helping people realize their dream</p>
  <div class="ph thumb-art" style="left:45px;top:45px" role="img" aria-label="Illustration of a thumbs up with stars"></div>
  <h2 class="dozen-title" style="left:228px;top:52px;color:var(--blue)">My Top<br>Dozen for<br>2024</h2>
  <ul class="bullets dozen" style="left:232px;top:204px">
    <li>Pet Options</li><li>Real Estate Options</li><li>Mental Health</li>
  </ul>
  <ul class="bullets dozen" style="left:382px;top:204px">
    <li>Pet Options</li><li>Real Estate Options</li><li>Mental Health</li>
  </ul>
  <div class="brand">UnitQuest<span class="dot"></span></div>
</section>

<section class="slide navy">
  <p class="tagline">Helping people realize their dream</p>
  <h2 class="dozen-title" style="left:54px;top:56px;color:#fff">My Top<br>Dozen for<br><span class="hl">2024</span></h2>
  <div class="ph thumb-art" style="left:271px;top:51px" role="img" aria-label="Illustration of a thumbs up with stars"></div>
  <ul class="bullets dozen" style="left:54px;top:222px">
    <li>Emergency Restoration</li><li>Low Status Options</li><li>Home Services</li>
  </ul>
  <ul class="bullets dozen" style="left:243px;top:222px">
    <li>Rental Options</li><li>Clothing Recyling</li><li>Food Trucks/Restaurants</li>
  </ul>
  <div class="brand">UnitQuest<span class="dot"></span></div>
</section>

<section class="slide dark">
  <div class="backdrop stars" role="img" aria-label="Long-exposure photo of star trails circling the night sky"></div>
  <p class="thanks">THANK YOU</p>
  <div class="brand" style="right:26px;bottom:20px">UnitQuest<span class="dot"></span></div>
</section>

</main>
</body>
</html>
```